Commercial Real Estate

We need a business card design for a new commercial real estate business that specializes in apartment building brokerage. Not individual units but the entire complex. We find and represent the owners existing buildings and well as new buyers for those buildings. The design should convey trust, integrity, knowledge and growth. It should be easily read.

Target Market(s)

40 to 65 years old

Industry/Entity Type

Real Estate

```html
<!DOCTYPE html>
<html lang="en">
<head>
<meta charset="utf-8">
<title>Ridgeline Property Investments – Business Card</title>
<link rel="stylesheet" href="https://fonts.googleapis.com/css2?family=Libre+Baskerville:wght@400;700&family=Lato:wght@400&display=swap">
<style>
  :root {
    --backdrop: #e9ecec;
    --card-white: #ffffff;
    --aqua-light: #9ff0ec;
    --aqua: #7fdcd8;
    --aqua-deep: #6ccfcb;
    --ink: #3f4b4b;
    --ink-soft: #2f3a3a;
    --teal-text: #3a9f9c;
    --shadow: rgba(30, 45, 45, 0.18);
  }
  * { box-sizing: border-box; margin: 0; padding: 0; }
  html, body {
    width: 1200px;
    height: 800px;
    overflow: hidden;
    background: var(--backdrop);
  }
  .stage {
    width: 1200px;
    height: 800px;
    display: flex;
    align-items: center;
    justify-content: center;
  }
  .business-card {
    width: 900px;
    height: 514px;
    display: flex;
    box-shadow: 0 14px 40px var(--shadow);
    font-family: "Libre Baskerville", Georgia, serif;
    color: var(--ink);
  }
  .brand-panel {
    width: 38%;
    background: var(--card-white);
    display: flex;
    flex-direction: column;
    align-items: center;
    justify-content: flex-end;
    padding: 0 30px 58px;
    text-align: center;
  }
  .brand-name {
    display: flex;
    flex-direction: column;
    align-items: center;
    gap: 14px;
    margin-bottom: 26px;
  }
  .brand-mark {
    width: 34px;
    height: 34px;
    background: var(--aqua-deep);
  }
  .brand-wordmark {
    font-weight: 700;
    font-size: 28px;
    line-height: 1.25;
    letter-spacing: 1px;
    color: var(--ink);
  }
  .brand-wordmark .brand-line {
    display: block;
    font-size: 20px;
    letter-spacing: 2px;
  }
  .office-address {
    font-style: normal;
    font-size: 17px;
    line-height: 1.5;
    color: var(--teal-text);
  }
  .contact-panel {
    width: 62%;
    background: linear-gradient(160deg, var(--aqua-light) 0%, var(--aqua) 55%, var(--aqua-deep) 100%);
    padding: 72px 56px 0 60px;
    display: flex;
    flex-direction: column;
    align-items: flex-end;
    text-align: right;
  }
  .agent-name {
    font-size: 30px;
    font-weight: 400;
    color: var(--ink);
    text-shadow: 0 1px 0 rgba(255,255,255,0.8);
  }
  .agent-title {
    font-family: "Lato", Arial, sans-serif;
    font-size: 16px;
    color: var(--ink-soft);
    margin-top: 2px;
  }
  .phone-list {
    list-style: none;
    margin-top: 44px;
    font-size: 22px;
    line-height: 1.45;
  }
  .phone-list .label { font-weight: 700; }
  .web-list {
    list-style: none;
    margin-top: 54px;
    font-size: 18px;
    line-height: 1.55;
  }
  .web-list .site { font-weight: 700; font-size: 19px; }
</style>
</head>
<body>
  <main class="stage">
    <article class="business-card">
      <section class="brand-panel">
        <div class="brand-name">
          <span class="brand-mark" aria-hidden="true"></span>
          <span class="brand-wordmark">RIDGELINE<span class="brand-line">Property Investments</span></span>
        </div>
        <address class="office-address">18 Alder Street Suite 100<br>Lakewood, CO 80401</address>
      </section>
      <section class="contact-panel">
        <h1 class="agent-name">Daniel Hartwell</h1>
        <p class="agent-title">Broker Associate</p>
        <ul class="phone-list">
          <li><span class="label">Phone:</span> 303-555-0142</li>
          <li><span class="label">Fax:</span> 720-555-0187</li>
        </ul>
        <ul class="web-list">
          <li>Email: daniel@ridgelinerealty.com</li>
          <li class="site">www.ridgelinerealty.com</li>
        </ul>
      </section>
    </article>
  </main>
</body>
</html>
```